New Fun, Positive, energised looking Business Card Needed for High Achiever Coach

I am looking for a two sided full colour business card. I am self employed and have recently re branded my 1-2-1 work re-vitalising high achievers. My target client base for these cards is therefore high achievers - usually aged 40 -55, they are often entrepreneurs, CEO or work in banking and finance and 2/3 are male. I work with them on 90 day or 6 month coaching programs to help them live their success in a healthier, more sustainable and fulfiiled way. They pay for this privately so though they are corporate types the cards need not look 'corporate'. I want to portray the idea of transformation, vitality and re-connecting.
You can get a feel for the look I like on my new website: morvenlisk.co.uk
I want to use this logo with strapline (Re-Vitalising High Achievers) (I purchased off Logoharbor) and font/ colours (the turquoise and green).
Details to include on the card:
www.morvenlisk.co.uk
+44 7915 302618
morven@morvenlisk.co.uk
skype: morvenlisk
I'd also like to include:
Do you struggle to switch off? Want to be healthier and feel fitter? Want closer relationships? More clarity over the direction you are headed? I can help you do these things using integrated mind-body techniques. Visit morvenlisk.co.uk TODAY to apply for a FREE Breakthrough session.
BUT if that is too much text for a card I am open to advice/ammendments.
Updates
Thanks for your design - I am considering them. PLease change the wording to :

```html
<!DOCTYPE html>
<html lang="en">
<head>
<meta charset="utf-8">
<title>Morven Lisk – Business Card Options</title>
<link href="https://fonts.googleapis.com/css2?family=Open+Sans:wght@400;600;700&display=swap" rel="stylesheet">
<style>
  :root {
    --backdrop: #5b3424;
    --card: #ffffff;
    --turquoise: #0aa3c6;
    --green: #5dbb6a;
    --ink: #3b3b3b;
    --muted: #555555;
    --rule: #9a9a9a;
    --label: #ffffff;
    --social: #4d7fbf;
    --ghost: #ececec;
  }
  * { margin: 0; padding: 0; box-sizing: border-box; }
  html, body {
    width: 1200px; height: 812px; overflow: hidden;
    background: var(--backdrop);
    font-family: "Open Sans", Arial, sans-serif;
  }
  .board { position: relative; width: 1200px; height: 812px; }

  .option-label {
    position: absolute; color: var(--label);
    font-size: 36px; font-weight: 400; line-height: 1;
  }

  .card {
    position: absolute; width: 511px; height: 291px;
    background: var(--card); overflow: hidden;
    box-shadow: 0 2px 6px rgba(0,0,0,.35);
  }
  .card--one   { left: 53px;  top: 99px; }
  .card--two   { left: 607px; top: 105px; }
  .card--three { left: 53px;  top: 439px; }
  .card--back  { left: 612px; top: 447px; }

  .brand {
    position: absolute; left: 20px; top: 38px; width: 200px;
    text-align: center;
  }
  .brand__dot {
    width: 58px; height: 58px; border-radius: 50%;
    background: var(--green); margin: 0 auto 14px;
  }
  .brand__name {
    color: var(--turquoise); font-size: 23px; font-weight: 700;
  }

  .divider {
    position: absolute; left: 243px; top: 42px; width: 2px; height: 138px;
    background: linear-gradient(to bottom, transparent, var(--rule), transparent);
  }

  .contact {
    position: absolute; left: 265px; top: 66px; list-style: none;
    color: var(--ink); font-size: 17px;
  }
  .contact li { display: flex; align-items: center; height: 33px; }
  .contact svg { width: 15px; height: 15px; margin-right: 6px; flex: none; }
  .contact .follow { font-size: 14.5px; color: var(--muted); }

  .social { display: inline-flex; gap: 4px; margin-left: 8px; }
  .social span { width: 16px; height: 16px; background: var(--social); border-radius: 2px; }

  .handle-mark { width: 14px; height: 14px; background: var(--turquoise); border-radius: 2px; margin-right: 7px; }

  .wave { position: absolute; left: 0; bottom: 0; width: 511px; height: 291px; }

  .web {
    position: absolute; right: 26px; bottom: 14px;
    color: #fff; font-size: 18px; font-weight: 600; letter-spacing: .5px;
  }
  .follow-band {
    position: absolute; right: 28px; bottom: 12px; text-align: right;
    color: #fff; font-size: 14.5px;
  }
  .follow-band .social { margin: 6px 0 0; }
  .follow-band .social span { background: var(--social); outline: 1px solid #fff; }

  .pitch {
    position: absolute; inset: 0; text-align: center;
    color: var(--ink); font-size: 16.5px; line-height: 23px; padding-top: 40px;
  }
  .pitch p + p { margin-top: 14px; }
  .pitch strong { font-weight: 700; }
  .pitch__ghost {
    position: absolute; left: 175px; top: 20px; width: 160px; height: 250px;
    border-radius: 50%; background: var(--ghost);
  }
</style>
</head>
<body>
<main class="board">

  <h2 class="option-label" style="left:207px; top:40px;">Option#1</h2>
  <h2 class="option-label" style="left:783px; top:40px;">Option#2</h2>
  <h2 class="option-label" style="left:238px; top:755px;">Option#3</h2>

  <!-- Option 1 front -->
  <section class="card card--one">
    <div class="brand"><div class="brand__dot"></div><div class="brand__name">Morven Lisk</div></div>
    <div class="divider"></div>
    <ul class="contact">
      <li><svg viewBox="0 0 16 16"><path d="M4 1l3 3-2 2c1 2 3 4 5 5l2-2 3 3-2 2C7 14 2 9 2 3z" fill="#444"/></svg>+44 7915 302618</li>
      <li><svg viewBox="0 0 16 16"><path d="M1 6l7-4 7 4v8H1z" fill="#444"/><path d="M2 7l6 4 6-4" stroke="#fff" fill="none"/></svg>morven@morvenlisk.co.uk</li>
      <li class="follow">Follow us on <span class="social"><span></span><span></span><span></span><span></span></span></li>
    </ul>
    <svg class="wave" viewBox="0 0 511 291" aria-hidden="true">
      <path d="M0 256 C140 274 300 226 511 218 L511 232 C330 236 160 286 0 270Z" fill="var(--green)"/>
      <path d="M0 276 C160 284 330 232 511 238 L511 291 L0 291Z" fill="var(--turquoise)"/>
      <path d="M160 276 C280 258 380 234 470 228" stroke="var(--turquoise)" stroke-width="2" fill="none"/>
    </svg>
    <div class="web">www.morvenlisk.co.uk</div>
  </section>

  <!-- Option 2 front -->
  <section class="card card--two">
    <div class="brand"><div class="brand__dot"></div><div class="brand__name">Morven Lisk</div></div>
    <div class="divider"></div>
    <ul class="contact">
      <li><svg viewBox="0 0 16 16"><path d="M4 1l3 3-2 2c1 2 3 4 5 5l2-2 3 3-2 2C7 14 2 9 2 3z" fill="#444"/></svg>+44 7915 302618</li>
      <li style="height:37px"><svg viewBox="0 0 16 16"><path d="M1 6l7-4 7 4v8H1z" fill="#444"/><path d="M2 7l6 4 6-4" stroke="#fff" fill="none"/></svg>morven@morvenlisk.co.uk</li>
      <li style="height:37px"><span class="handle-mark"></span>morvenlisk</li>
    </ul>
    <svg class="wave" viewBox="0 0 511 291" aria-hidden="true">
      <path d="M0 256 C140 274 300 226 511 218 L511 232 C330 236 160 286 0 270Z" fill="var(--green)"/>
      <path d="M0 276 C160 284 330 232 511 238 L511 291 L0 291Z" fill="var(--turquoise)"/>
      <path d="M160 276 C280 258 380 234 470 228" stroke="var(--turquoise)" stroke-width="2" fill="none"/>
    </svg>
    <div class="web">www.morvenlisk.co.uk</div>
  </section>

  <!-- Option 3 front -->
  <section class="card card--three">
    <div class="brand"><div class="brand__dot"></div><div class="brand__name">Morven Lisk</div></div>
    <div class="divider"></div>
    <ul class="contact">
      <li style="height:36px"><svg viewBox="0 0 16 16"><path d="M4 1l3 3-2 2c1 2 3 4 5 5l2-2 3 3-2 2C7 14 2 9 2 3z" fill="#444"/></svg>+44 7915 302618</li>
      <li style="height:36px"><svg viewBox="0 0 16 16"><path d="M1 6l7-4 7 4v8H1z" fill="#444"/><path d="M2 7l6 4 6-4" stroke="#fff" fill="none"/></svg>morven@morvenlisk.co.uk</li>
      <li style="height:36px"><svg viewBox="0 0 16 16"><circle cx="8" cy="8" r="6.5" fill="none" stroke="#444" stroke-width="1.4"/><path d="M1.5 8h13M8 1.5c-3 3.5-3 9.5 0 13M8 1.5c3 3.5 3 9.5 0 13" fill="none" stroke="#444" stroke-width="1.1"/></svg>www.morvenlisk.co.uk</li>
    </ul>
    <svg class="wave" viewBox="0 0 511 291" aria-hidden="true">
      <path d="M0 256 C140 274 300 226 511 218 L511 232 C330 236 160 286 0 270Z" fill="var(--green)"/>
      <path d="M0 276 C160 284 330 232 511 238 L511 291 L0 291Z" fill="var(--turquoise)"/>
      <path d="M160 276 C280 258 380 234 470 228" stroke="var(--turquoise)" stroke-width="2" fill="none"/>
    </svg>
    <div class="follow-band">Follow us on<br><span class="social"><span></span><span></span><span></span><span></span></span></div>
  </section>

  <!-- Shared back -->
  <section class="card card--back">
    <div class="pitch__ghost"></div>
    <div class="pitch">
      <p>Do you struggle to switch off?<br>Want to be healthier and&nbsp; feel fitter?<br>Want closer relationships?<br>More clarity over the direction you are headed?</p>
      <p>Let me help you reach these goals using integrated<br>mind-body techniques.</p>
      <p>Visit <strong>morvenlisk.co.uk</strong>&nbsp; TODAY to apply for a<br>FREE Breakthrough session.</p>
    </div>
  </section>

</main>
</body>
</html>
```